Website - Loretta Dubrow

I need a website that has multiple pages and easy for me to update pictures, content and blogs as an ongoing basis’s.
It will have videos and needs to be compatible to view easily and aesthetically on mobile phones.
Please refer to this website for inspiration www.quinnafernsby.com

Coding

Coded - Design and coding required

Number of Pages Required

5+ page

Other font styles liked:
• Refer to website provided as inspiration

Requirements
Must have
• Please use stock images for now to do design, but I will be providing all imagery, videos and content

```html
<!DOCTYPE html>
<html lang="en">
<head>
<meta charset="utf-8">
<title>Loretta Dubrow</title>
<link href="https://fonts.googleapis.com/css2?family=Poppins:wght@300;400;500;600;700&display=swap" rel="stylesheet">
<style>
:root{
  --magenta:#e52ef0;
  --violet:#5a10e8;
  --brand:#b01cf0;
  --ink:#1c1230;
  --navy:#1d0b4e;
  --muted:#6b6b74;
  --hero-bg:#e9e9ef;
  --white:#ffffff;
  --footer:#14001f;
  --play:#d42020;
  --grad:linear-gradient(90deg,var(--magenta),var(--violet));
  --btn-grad:linear-gradient(90deg,#f08cf2,#9b55ee);
}
*{margin:0;padding:0;box-sizing:border-box}
html,body{width:1200px;height:2565px;overflow:hidden}
body{position:relative;background:var(--white);font-family:'Poppins',sans-serif;color:var(--ink)}
.abs{position:absolute}
.hero-band{left:0;top:0;width:1200px;height:625px;background:var(--hero-bg)}
.brand-name{left:145px;top:18px;font-size:31px;font-weight:600;color:var(--brand);letter-spacing:.3px}
.main-nav{right:142px;top:32px;display:flex;gap:31px;font-size:13px;font-weight:400;color:var(--ink)}
.hero-title{right:612px;top:160px;text-align:right;font-size:125px;font-weight:700;line-height:92px;letter-spacing:-2px;
  background:var(--grad);-webkit-background-clip:text;background-clip:text;color:transparent}
.play-btn{left:525px;top:389px;width:62px;height:62px}
.frame{border:12px solid transparent;border-image:linear-gradient(135deg,var(--magenta),var(--violet)) 1}
.hero-frame{left:655px;top:100px;width:327px;height:445px}
.photo{background:linear-gradient(160deg,#4a3a3a,#2a1f1f)}
.hero-photo{left:676px;top:110px;width:358px;height:515px;background:linear-gradient(170deg,#d8d6dc 0%,#3a2622 35%,#2a1a18 60%,#1f8a6e 85%,#e2e2e2 100%)}
.about-back{left:145px;top:700px;width:374px;height:406px;background:linear-gradient(120deg,#5a4030,#c78b7c 45%,#3a2a22)}
.about-frame{left:275px;top:553px;width:327px;height:445px;background:var(--white)}
.about-photo{left:287px;top:565px;width:303px;height:421px;background:linear-gradient(160deg,#6d5038,#c08a66 50%,#5a3e2c)}
.section-title{left:649px;top:733px;font-size:25px;font-weight:500;letter-spacing:1.5px;color:var(--navy)}
.title-rule{left:649px;top:776px;width:91px;height:3px;background:var(--grad)}
.about-copy{left:649px;top:804px;width:415px;font-size:13.4px;font-weight:300;line-height:22.4px;letter-spacing:.5px;color:var(--muted)}
.read-more{width:121px;height:38px}
.read-more .outline{position:absolute;left:0;top:0;width:121px;height:38px;border:1px solid var(--ink)}
.read-more .fill{position:absolute;left:5px;top:5px;width:120px;height:37px;background:var(--btn-grad);color:var(--white);
  font-size:13px;font-weight:400;letter-spacing:.5px;display:flex;align-items:center;justify-content:center}
.post-photo-1{left:595px;top:1106px;width:605px;height:399px;background:linear-gradient(180deg,#d2d2d2,#f0f0f0 40%,#2a3850 80%,#d9d9d9)}
.post-photo-2{left:0;top:1506px;width:595px;height:399px;background:linear-gradient(90deg,#2d3238 0%,#2d3238 14%,#c99e86 30%,#d7b59e 55%,#4a2e2e 80%,#e8e4e0 100%)}
.notch{width:0;height:0;border-top:22px solid transparent;border-bottom:22px solid transparent}
.notch-right{left:595px;top:1186px;border-left:20px solid var(--white)}
.notch-left{left:575px;top:1584px;border-right:20px solid var(--white)}
.post-title{font-size:24px;font-weight:400;color:var(--ink)}
.post-date{font-size:14.5px;font-weight:400;color:var(--ink)}
.post-copy{width:410px;font-size:14.5px;font-weight:400;line-height:24px;color:var(--ink)}
.gallery{left:0;top:1905px;width:1200px;height:254px;display:flex}
.gallery div{width:300px;height:254px}
.g1{background:linear-gradient(135deg,#8a1ee0,#c83bd8 50%,#6a12c0)}
.g2{background:linear-gradient(180deg,#a68a6a,#e9e5e0 55%,#3a4a2a)}
.g3{background:linear-gradient(135deg,#8a1240,#e0306a 50%,#3a0a20)}
.g4{background:linear-gradient(135deg,#111,#6a4030 50%,#111)}
.social-tag{left:452px;top:2127px;width:210px;height:50px;background:var(--grad);color:var(--white);font-size:26px;font-weight:300;
  display:flex;align-items:center;justify-content:center}
.news-title{left:0;top:2222px;width:1200px;text-align:center;font-size:34px;font-weight:300;letter-spacing:2.5px;color:var(--ink)}
.news-copy{left:0;top:2284px;width:1200px;text-align:center;font-size:15.5px;font-weight:300;line-height:26px;color:var(--ink)}
.email-field{left:329px;top:2352px;width:346px;height:52px;border:1px solid #c9c9cf;font-size:17px;font-weight:300;letter-spacing:1px;color:#8a8a92;
  padding-left:20px;display:flex;align-items:center}
.signup{left:703px;top:2348px;width:168px;height:58px}
.signup .outline{position:absolute;left:0;top:0;width:163px;height:53px;border:1px solid var(--ink)}
.signup .fill{position:absolute;left:6px;top:6px;width:162px;height:52px;background:var(--btn-grad);color:var(--white);font-size:17px;font-weight:400;letter-spacing:1px;
  display:flex;align-items:center;justify-content:center}
.site-footer{left:0;top:2487px;width:1200px;height:78px;background:var(--footer);color:var(--white);font-size:13px;font-weight:400;
  display:flex;align-items:center;justify-content:center}
</style>
</head>
<body>
  <div class="abs hero-band"></div>
  <div class="abs brand-name">lorettadubrow</div>
  <nav class="abs main-nav"><span>Home</span><span>About Me</span><span>Gallery</span><span>Blog</span><span>Stories</span><span>Contact Me</span></nav>

  <h1 class="abs hero-title">Bold<br>Brave</h1>
  <svg class="abs play-btn" viewBox="0 0 62 62" aria-label="Play video"><circle cx="31" cy="31" r="31" fill="var(--play)"/><path d="M24 19 L43 31 L24 43 Z" fill="#fff"/></svg>

  <div class="abs frame hero-frame"></div>
  <div class="abs hero-photo" role="img" aria-label="Portrait of a young woman with a crown and pageant sash"></div>

  <div class="abs about-back" role="img" aria-label="Woman in a pink satin dress smiling over her shoulder"></div>
  <div class="abs frame about-frame"></div>
  <div class="abs about-photo" role="img" aria-label="Close-up portrait with wavy hair"></div>

  <h2 class="abs section-title">lorettadubrow</h2>
  <div class="abs title-rule"></div>
  <p class="abs about-copy">Lorem Ipsum is simply dummy text of the printing and typesetting industry. Lorem Ipsum has been the industry's standard dummy text ever since the 1500s, when an unknown printer took a galley of type and scrambled it to make a type specimen book. It has survived not only five centuries, but also the leap into electronic typesetting, remaining essentially unchanged.</p>
  <div class="abs read-more" style="left:649px;top:990px"><div class="outline"></div><div class="fill">Read More</div></div>

  <div class="abs post-photo-1" role="img" aria-label="Woman seated on white drapery"></div>
  <div class="abs notch notch-right"></div>
  <h3 class="abs post-title" style="left:143px;top:1190px">Neque porro quisquam est</h3>
  <div class="abs post-date" style="left:144px;top:1232px">Apr 23, 2020</div>
  <p class="abs post-copy" style="left:144px;top:1268px">Lorem Ipsum is simply dummy text of the printing and typesetting industry. Lorem Ipsum has been the indus-try's standard dummy text ever since the</p>
  <div class="abs read-more" style="left:144px;top:1372px"><div class="outline"></div><div class="fill">Read More</div></div>

  <div class="abs post-photo-2" role="img" aria-label="Close-up selfie portrait with dark hair"></div>
  <div class="abs notch notch-left"></div>
  <h3 class="abs post-title" style="left:728px;top:1588px">Neque porro quisquam est</h3>
  <div class="abs post-date" style="left:729px;top:1630px">Apr 23, 2020</div>
  <p class="abs post-copy" style="left:729px;top:1666px">Lorem Ipsum is simply dummy text of the printing and typesetting industry. Lorem Ipsum has been the indus-try's standard dummy text ever since the</p>
  <div class="abs read-more" style="left:729px;top:1770px"><div class="outline"></div><div class="fill">Read More</div></div>

  <div class="abs gallery">
    <div class="g1" role="img" aria-label="Portrait under purple light"></div>
    <div class="g2" role="img" aria-label="Two friends at a graduation"></div>
    <div class="g3" role="img" aria-label="Friends in a neon-lit bar"></div>
    <div class="g4" role="img" aria-label="Two women posing at an evening event"></div>
  </div>
  <div class="abs social-tag">@snapfeed</div>

  <h2 class="abs news-title">Sign up for newsletter</h2>
  <p class="abs news-copy">Neque porro quisquam est qui dolorem ipsum quia dolor sit amet,<br>consectetur, adipisci velit..</p>
  <div class="abs email-field">Email Address</div>
  <div class="abs signup"><div class="outline"></div><div class="fill">Sign Up</div></div>

  <footer class="abs site-footer">Loretta Dubrow © 2021 All Rights Reserved.</footer>
</body>
</html>
```